Business card for my new company (Accounting firm)

I need a business card for my new business Brightwell Advisory and Ledger SA. Our services are accounting, tax, audit and financial management. Our customers are small companies, start-ups and new companies. The final design has to show financial security, trust and growth. Please find our logo attached to the business card. Text for the business card: Brightwell Advisory and Ledger SA Tomas Varenholt Director and Founder Certified Accountant Tel. 022 418 57 34 tv@clairevalconseil.ch www.clairevalconseil.ch Rue des Vergières 27 1201 Geneva
Target Market(s)
Our customers are small companies, start-ups and new companies.
Industry/Entity Type
Finance And Accounting
Contact Information for Business Card
Claireval Conseil et Comptes SA
Tomas Varenholt
Directeur et Fondateur
Expert-comptable diplômé
Tél. 022 418 57 34
tv@clairevalconseil.ch
www.clairevalconseil.ch
Rue des Vergières 27
1201 Genève

```html
<!DOCTYPE html>
<html lang="fr">
<head>
<meta charset="utf-8">
<title>Claireval Conseil et Comptes – carte de visite</title>
<link rel="stylesheet" href="https://fonts.googleapis.com/css2?family=Roboto:wght@400;500;700&display=swap">
<style>
  :root {
    --backdrop: #d9dadc;
    --card-white: #ffffff;
    --brand-blue: #2ba3dd;
    --brand-sky: #3cc3ea;
    --brand-deep: #2a8fd6;
    --ink: #4a4a4a;
    --ink-soft: #5c5c5c;
    --rule: #d4d4d4;
  }
  * { box-sizing: border-box; margin: 0; padding: 0; }
  html, body { width: 1200px; height: 801px; overflow: hidden; }
  body {
    background: var(--backdrop);
    font-family: "Roboto", Arial, sans-serif;
    position: relative;
  }
  .card {
    position: absolute;
    top: 246px;
    width: 540px;
    height: 309px;
    box-shadow: 0 6px 18px rgba(0,0,0,.18);
    overflow: hidden;
  }
  /* Front */
  .card--front { left: 45px; background: var(--card-white); }
  .brand {
    position: absolute;
    left: 0; top: 0;
    width: 270px; height: 100%;
    display: flex;
    align-items: center;
    justify-content: center;
    gap: 10px;
  }
  .brand__square {
    width: 22px; height: 22px;
    background: var(--brand-blue);
  }
  .brand__name {
    font-weight: 500;
    font-size: 30px;
    letter-spacing: 2px;
    color: var(--ink);
  }
  .divider {
    position: absolute;
    left: 272px; top: 40px;
    width: 1px; height: 229px;
    background: linear-gradient(to bottom, transparent, var(--rule) 20%, var(--rule) 80%, transparent);
    box-shadow: 3px 0 6px rgba(0,0,0,.06);
  }
  .details {
    position: absolute;
    left: 300px; top: 62px;
    color: var(--ink-soft);
    font-size: 12.5px;
    line-height: 1.35;
  }
  .details__name {
    font-size: 19px;
    font-weight: 700;
    color: var(--brand-blue);
    margin-bottom: 3px;
  }
  .details__group { margin-bottom: 12px; }
  .contact { list-style: none; }
  .contact li { display: flex; align-items: center; gap: 7px; }
  .contact svg { width: 11px; height: 11px; flex: none; }
  /* Back */
  .card--back {
    left: 615px;
    background: linear-gradient(135deg, var(--brand-sky) 0%, var(--brand-blue) 55%, var(--brand-deep) 100%);
  }
  .card__pattern {
    position: absolute; inset: 0;
    background: linear-gradient(135deg, rgba(255,255,255,.06), rgba(255,255,255,0) 60%);
  }
  .card__mark {
    position: absolute;
    right: 30px; bottom: 34px;
    font-weight: 500;
    font-size: 18px;
    letter-spacing: 1.5px;
    color: var(--card-white);
  }
</style>
</head>
<body>
  <section class="card card--front" aria-label="Recto de la carte">
    <div class="brand">
      <span class="brand__square"></span>
      <span class="brand__name">CLAIREVAL</span>
    </div>
    <div class="divider"></div>
    <div class="details">
      <div class="details__group">
        <p class="details__name">Tomas Varenholt</p>
        <p>Directeur et Fondateur</p>
        <p>Expert-comptable diplômé</p>
      </div>
      <div class="details__group">
        <p>Rue des Vergières 27</p>
        <p>1201 Genève</p>
      </div>
      <ul class="contact">
        <li>
          <svg viewBox="0 0 24 24" fill="var(--brand-blue)" aria-hidden="true"><path d="M6.6 10.8a15 15 0 0 0 6.6 6.6l2.2-2.2a1 1 0 0 1 1-.25 11.4 11.4 0 0 0 3.6.57 1 1 0 0 1 1 1V20a1 1 0 0 1-1 1A17 17 0 0 1 3 4a1 1 0 0 1 1-1h3.5a1 1 0 0 1 1 1c0 1.25.2 2.45.57 3.57a1 1 0 0 1-.25 1z"/></svg>
          022 418 57 34
        </li>
        <li>
          <svg viewBox="0 0 24 24" fill="var(--brand-blue)" aria-hidden="true"><path d="M2 5h20v14H2z" opacity=".9"/><path d="M2 5l10 8 10-8" fill="none" stroke="#fff" stroke-width="2"/></svg>
          tv@clairevalconseil.ch
        </li>
        <li>
          <svg viewBox="0 0 24 24" aria-hidden="true"><circle cx="12" cy="12" r="10" fill="var(--brand-blue)"/><path d="M2 12h20M12 2c3 3 3 17 0 20M12 2c-3 3-3 17 0 20" fill="none" stroke="#fff" stroke-width="1.5"/></svg>
          www.clairevalconseil.ch
        </li>
      </ul>
    </div>
  </section>

  <section class="card card--back" aria-label="Verso de la carte">
    <div class="card__pattern" role="img" aria-label="Motif répété discret de l'emblème de la marque sur fond bleu"></div>
    <span class="card__mark">CLAIREVAL</span>
  </section>
</body>
</html>
```